My company is throwing a party. The name is 80/20 (80% Calypso & 20% Whatever Remains)

I seek a flyer that shows this will be a very elegant, upscale event and at the same time high energy, great reggae music and dancing.

I need this flyer to be 650 pixels wide & any length, High resolution (1MB) for printing on a 4" x 6" flyer.

Target Market(s)

Fans of reggae music

Industry/Entity Type

Printing

Requirements
Must have
• Radiant Holdings Presents:
80/20
Upscale Reggae Soiree
80% Calypso - 20% Whatever Remains

Saturday May 4th, 10pm - 3am

The Lantern: 412 1/2 North Hollis Blvd, OKC

Dress to impress! We reserve the right to refuse entry

Free Entry: 1st 50 Ladies On VIP Guestlist - Discounted Early Bird Online Tickets - For Bottle Service Reservation: http://islandnight.ticketmarlo.com

More info? 405-555-0187

```html
<!DOCTYPE html>
<html lang="en">
<head>
<meta charset="utf-8">
<title>80/20 Upscale Reggae Soiree</title>
<link rel="stylesheet" href="https://fonts.googleapis.com/css2?family=Anton&family=Open+Sans:ital,wght@0,400;0,700;1,400&family=Rubik+Dirt&display=swap">
<style>
  :root {
    --bg: #000000;
    --ink: #f2f2f2;
    --green: #43a02f;
    --ghost: #2b2b2b;
    --banner: #f2e51a;
    --red: #c8152b;
  }
  html, body { margin: 0; padding: 0; overflow: hidden; background: var(--bg); }
  .flyer {
    position: relative;
    width: 800px;
    height: 1200px;
    overflow: hidden;
    background: var(--bg);
    color: var(--ink);
    font-family: "Open Sans", Arial, sans-serif;
  }
  .flyer p, .flyer h1 { margin: 0; }
  .brand {
    position: absolute;
    top: 62px;
    left: 0;
    width: 100%;
    display: flex;
    justify-content: center;
    align-items: center;
    gap: 12px;
    font-size: 26px;
    font-weight: 400;
    color: var(--ink);
  }
  .brand-dot {
    width: 20px;
    height: 20px;
    border: 2px solid var(--ink);
    border-radius: 50%;
  }
  .ghost-title, .main-title {
    position: absolute;
    left: 0;
    width: 100%;
    text-align: center;
    font-family: "Anton", "Arial Narrow", sans-serif;
    font-weight: 400;
    line-height: 1;
    white-space: nowrap;
  }
  .ghost-title {
    top: 250px;
    font-size: 560px;
    color: var(--ghost);
    transform: scaleX(0.95);
    letter-spacing: -4px;
  }
  .main-title {
    top: 186px;
    font-size: 340px;
    color: var(--green);
    transform: scaleX(0.7);
    letter-spacing: -4px;
  }
  .banner {
    position: absolute;
    top: 540px;
    left: 67px;
    width: 680px;
    height: 113px;
  }
  .banner svg { position: absolute; inset: 0; }
  .banner-text {
    position: absolute;
    inset: 0;
    display: flex;
    align-items: center;
    justify-content: center;
    font-family: "Rubik Dirt", Impact, sans-serif;
    font-size: 44px;
    color: var(--red);
    text-transform: uppercase;
    letter-spacing: 1px;
  }
  .info {
    position: absolute;
    left: 0;
    width: 100%;
    text-align: center;
    font-size: 25px;
    line-height: 1.2;
  }
  .tagline { top: 700px; }
  .tagline .pct { color: var(--green); font-weight: 700; }
  .date { top: 750px; font-weight: 700; }
  .dress { top: 815px; }
  .entry { top: 880px; line-height: 44px; }
  .info strong { font-weight: 700; }
  .info sup { font-size: 14px; }
  .diamond { color: var(--green); }
  .url { font-style: italic; }
  .footer {
    position: absolute;
    top: 1128px;
    font-size: 21px;
    display: flex;
    align-items: center;
    gap: 12px;
  }
  .venue { left: 30px; }
  .phone { left: 572px; }
  .footer svg { fill: var(--ink); }
</style>
</head>
<body>
<main class="flyer">
  <div class="brand"><span class="brand-dot"></span>Radiant Holdings</div>

  <div class="ghost-title" aria-hidden="true">80/20</div>
  <h1 class="main-title">80/20</h1>

  <div class="banner">
    <svg viewBox="0 0 680 113" width="680" height="113" aria-hidden="true">
      <polygon fill="var(--banner)" points="4,8 40,2 90,10 140,3 200,9 260,2 330,8 400,3 460,10 520,2 580,8 640,3 676,9 672,30 679,55 671,80 678,108 630,104 570,111 500,105 430,111 360,104 290,110 220,104 150,111 90,104 30,110 2,105 8,80 1,55 7,30"/>
    </svg>
    <div class="banner-text">Upscale Reggae Soiree</div>
  </div>

  <p class="info tagline"><span class="pct">80%</span> Calypso - <span class="pct">20%</span> Whatever Remains</p>

  <p class="info date">Saturday May 4th, 10pm - 3am</p>

  <p class="info dress"><strong>Dress to impress!</strong> We reserve the right to refuse entry</p>

  <p class="info entry">
    <strong>Free Entry:</strong> 1<sup>st</sup> 50 Ladies On VIP Guestlist<br>
    <span class="diamond">&#9830;</span> Discounted Early Bird Online Tickets <span class="diamond">&#9830;</span> For<br>
    Bottle Service Reservation:<br>
    <span class="url">http://islandnight.ticketmarlo.com</span>
  </p>

  <div class="footer venue">
    <svg width="24" height="35" viewBox="0 0 26 38" aria-hidden="true">
      <path d="M13 0C5.8 0 0 5.8 0 13c0 9.5 13 25 13 25s13-15.5 13-25C26 5.8 20.2 0 13 0zm0 18a5 5 0 1 1 0-10 5 5 0 0 1 0 10z"/>
    </svg>
    <span>The Lantern: 412 1/2 North Hollis Blvd, OKC</span>
  </div>

  <div class="footer phone">
    <svg width="30" height="34" viewBox="0 0 32 36" aria-hidden="true">
      <path d="M7 1l6 8-4 4c2 5 6 10 11 13l4-4 8 6-4 7c-14-1-27-16-28-30z"/>
    </svg>
    <span>405-555-0187</span>
  </div>
</main>
</body>
</html>
```